Vegan bakery needs business card

We need a business card design for my vegan bakery in Philadelphia Pa. We create amazing whole food plant based cuisine that is egg and dairy free. We use fruits, vegetables, healing herbs, nuts, natural sugars (date, turbinado, agave) and non bleached flours in our creations. Due to demand and interest in the Philadelphia area we created a late night vegan dessert delivery service named Bramble Vegan. We are the only business providing delicious vegan desserts delivered to your door at 1am!! We would like to see designs that use the color scheme in the logo. The final design should communicate the benefits of our products: dairy/egg free, plant based, healing herbs, amazing food.

```html
<!DOCTYPE html>
<html lang="en">
<head>
<meta charset="UTF-8">
<title>Bramble Vegan – Business Card</title>
<link rel="stylesheet" href="https://fonts.googleapis.com/css2?family=Questrial&display=swap">
<style>
  :root {
    --stage: #2b2b2d;
    --card: #0d0f15;
    --coral: #f2785c;
    --leaf: #6cbf4a;
    --ink: #f3f1ee;
    --muted: #d9d6d2;
  }
  * { box-sizing: border-box; margin: 0; padding: 0; }
  html, body {
    width: 1200px; height: 880px; overflow: hidden;
    background: var(--stage);
    font-family: "Questrial", "Century Gothic", sans-serif;
  }
  .stage {
    width: 1200px; height: 880px;
    display: flex; flex-direction: column; align-items: center;
    justify-content: center; gap: 32px;
  }
  .card {
    position: relative;
    width: 680px; height: 388px;
    background: var(--card);
    border-radius: 18px;
    box-shadow: 0 10px 30px rgba(0,0,0,.45);
    color: var(--ink);
  }
  .brand {
    display: flex; flex-direction: column; align-items: center; gap: 14px;
  }
  .brand-name {
    color: var(--coral);
    font-size: 34px; letter-spacing: .5px;
  }
  .brand-dot {
    width: 96px; height: 96px; border-radius: 50%;
    background: var(--coral);
  }

  /* Front face */
  .card-front .brand { position: absolute; left: 0; right: 0; top: 60px; }
  .card-front .products {
    position: absolute; left: 0; right: 0; top: 268px; text-align: center;
  }
  .products-title { color: var(--coral); font-size: 15px; letter-spacing: .5px; }
  .products-list { color: var(--ink); font-size: 16px; margin-top: 8px; }

  /* Back face */
  .card-back .brand { position: absolute; left: 60px; width: 250px; top: 70px; }
  .tagline {
    color: var(--leaf); font-size: 20px; line-height: 1.15; text-align: center;
  }
  .divider {
    position: absolute; left: 345px; top: 70px; width: 1px; height: 250px;
    background: var(--leaf);
  }
  .contact { position: absolute; left: 385px; top: 78px; }
  .person-name { color: var(--coral); font-size: 24px; }
  .person-role { font-size: 15px; color: var(--ink); margin-top: 2px; }
  .address { font-size: 15px; line-height: 1.35; margin-top: 28px; }
  .channels { list-style: none; margin-top: 14px; }
  .channels li {
    display: flex; align-items: center; gap: 10px;
    font-size: 15px; line-height: 1; margin-bottom: 7px;
  }
  .icon {
    width: 18px; height: 18px; border-radius: 50%;
    background: var(--coral);
    display: inline-flex; align-items: center; justify-content: center;
    flex: none;
  }
  .icon svg { width: 11px; height: 11px; }
</style>
</head>
<body>
<main class="stage">

  <section class="card card-front" aria-label="Card front">
    <div class="brand">
      <span class="brand-name">Bramble Vegan</span>
      <span class="brand-dot"></span>
    </div>
    <div class="products">
      <p class="products-title">OUR PRODUCTS</p>
      <p class="products-list">dairy/egg free, plant based, healing herbs, amazing food.</p>
    </div>
  </section>

  <section class="card card-back" aria-label="Card back">
    <div class="brand">
      <span class="brand-name">Bramble Vegan</span>
      <span class="brand-dot"></span>
      <p class="tagline">100% vegan<br>100% delicious</p>
    </div>
    <span class="divider"></span>
    <div class="contact">
      <p class="person-name">Nora Kellan</p>
      <p class="person-role">Director of Marketing</p>
      <p class="address">PO Box 48, Larch Street<br>Philadelphia, PA 19107</p>
      <ul class="channels">
        <li><span class="icon"><svg viewBox="0 0 12 12"><path d="M2.5 1.5l2 0 .8 2.2-1.2.9a6 6 0 0 0 3.3 3.3l.9-1.2 2.2.8 0 2a1 1 0 0 1-1 1A8.5 8.5 0 0 1 1.5 2.5a1 1 0 0 1 1-1z" fill="#0d0f15"/></svg></span>555-014-2271</li>
        <li><span class="icon"><svg viewBox="0 0 12 12"><rect x="1.5" y="3" width="9" height="6.5" rx="1" fill="none" stroke="#0d0f15" stroke-width="1.2"/><path d="M1.8 3.4L6 6.6l4.2-3.2" fill="none" stroke="#0d0f15" stroke-width="1.2"/></svg></span>hello@bramblevegan.com</li>
        <li><span class="icon"><svg viewBox="0 0 12 12"><circle cx="6" cy="6" r="4.5" fill="none" stroke="#0d0f15" stroke-width="1.1"/><ellipse cx="6" cy="6" rx="2" ry="4.5" fill="none" stroke="#0d0f15" stroke-width="1"/><path d="M1.5 6h9" stroke="#0d0f15" stroke-width="1"/></svg></span>www.bramblevegan.com</li>
      </ul>
    </div>
  </section>

</main>
</body>
</html>
```